Business Card Design (NEW FILES)

ATTENTION: New vector files are available. Please update your design to reflect/use the new (better resolution) logo images.

Seeking a unique and professional business card design for a commercial drone photography/videography business. The layout should feature
the logo (attached) and include the following information:
Owen Tarrick
614-502-7738
www.skylarkreelworks.example
NRD Certified Remote Pilot

Owen Tarrick

```html
<!DOCTYPE html>
<html lang="en">
<head>
<meta charset="utf-8">
<title>Skylark Reelworks – Business Card</title>
<link rel="stylesheet" href="https://fonts.googleapis.com/css2?family=Open+Sans:wght@400;600;800&display=swap">
<style>
  :root{
    --backdrop:#1f1f24;
    --navy:#15194a;
    --navy-deep:#10133b;
    --drone-blue:#3149b8;
    --drone-mid:#24358f;
    --orange:#ef8a45;
    --white:#ffffff;
  }
  *{box-sizing:border-box;margin:0;padding:0}
  html,body{width:1200px;height:780px;overflow:hidden}
  body{
    background:var(--backdrop);
    font-family:"Open Sans",Arial,sans-serif;
    color:var(--white);
    display:flex;align-items:center;justify-content:center;gap:36px;
  }
  .card{
    position:relative;width:560px;height:320px;border-radius:22px;
    background:var(--navy);
    box-shadow:0 4px 0 var(--orange),0 18px 36px rgba(0,0,0,.5);
    overflow:hidden;
  }

  /* front */
  .hero-art{
    position:absolute;left:28px;top:14px;width:470px;height:270px;
    border-radius:48% 52% 46% 54% / 42% 40% 60% 58%;
    background:
      radial-gradient(ellipse 38% 34% at 64% 34%,rgba(80,104,220,.75),transparent 70%),
      radial-gradient(ellipse 60% 55% at 40% 48%,rgba(49,73,184,.55),transparent 75%),
      linear-gradient(160deg,var(--drone-mid) 0%,rgba(36,53,143,.55) 45%,rgba(21,25,74,0) 85%);
    box-shadow:inset 0 0 0 2px rgba(80,104,220,.35);
  }
  .brand{
    position:absolute;display:flex;align-items:center;gap:10px;
    font-weight:600;letter-spacing:.06em;text-transform:uppercase;color:var(--white);
    white-space:nowrap;
  }
  .brand-dot{border-radius:50%;background:var(--orange);flex:none}
  .card-front .brand{left:200px;bottom:46px;font-size:22px}
  .card-front .brand-dot{width:13px;height:13px}

  /* back */
  .card-back .brand{left:34px;bottom:46px;font-size:28px}
  .card-back .brand-dot{width:16px;height:16px}
  .contact{position:absolute;right:0;top:40px;text-align:right}
  .name-row{display:flex;align-items:flex-start;justify-content:flex-end;gap:12px}
  .name{font-size:28px;font-weight:800;line-height:1.1}
  .name .first{color:var(--orange)}
  .accent-bar{width:24px;height:46px;background:var(--orange)}
  .role{font-size:15px;font-weight:600;margin:0 36px 0 0}
  .details{margin:12px 36px 0 0;font-size:14px;line-height:1.7}
  .details li{list-style:none;display:flex;justify-content:flex-end;align-items:center;gap:8px}
  .icon{width:13px;height:13px;flex:none}
</style>
</head>
<body>

<section class="card card-front" aria-label="Card front">
  <div class="hero-art" role="img" aria-label="Large drone illustration in deep and bright blue spanning the card"></div>
  <div class="brand"><span class="brand-dot"></span>Skylark Reelworks</div>
</section>

<section class="card card-back" aria-label="Card back">
  <div class="brand"><span class="brand-dot"></span>Skylark Reelworks</div>
  <div class="contact">
    <div class="name-row">
      <h1 class="name"><span class="first">Owen</span> Tarrick</h1>
      <span class="accent-bar"></span>
    </div>
    <p class="role">Owner</p>
    <ul class="details">
      <li>NRD Certified Remote Pilot</li>
      <li>Fully Insured</li>
      <li>614-502-7738
        <svg class="icon" viewBox="0 0 24 24" aria-hidden="true"><path fill="var(--orange)" d="M6.6 10.8a15 15 0 0 0 6.6 6.6l2.2-2.2a1 1 0 0 1 1-.25 11.4 11.4 0 0 0 3.6.57 1 1 0 0 1 1 1V20a1 1 0 0 1-1 1A17 17 0 0 1 3 4a1 1 0 0 1 1-1h3.5a1 1 0 0 1 1 1c0 1.25.2 2.45.57 3.57a1 1 0 0 1-.25 1z"/></svg>
      </li>
      <li>www.skylarkreelworks.example
        <svg class="icon" viewBox="0 0 24 24" aria-hidden="true"><circle cx="12" cy="12" r="9" fill="none" stroke="var(--orange)" stroke-width="2"/><path d="M3 12h18M12 3c3 3 3 15 0 18M12 3c-3 3-3 15 0 18" fill="none" stroke="var(--orange)" stroke-width="1.6"/></svg>
      </li>
    </ul>
  </div>
</section>

</body>
</html>
```